VORTEQ

It’s is a startup business. We design and build new products.

Target Market(s)

For my first two products, they are targeting the laundry market, hanger accessory, and new modern style clothes dryer. I also have a Pet Treat product at patent stage, and there are other products not yet started but will be more engineering based. Therefore from young adults to older population

Industry/Entity Type

Colours of website to match the logo (att)

Coding

Coded - Design and coding required

Number of Pages Required

1 page

Font styles to use
Other font styles liked:
• Some of the same font as the logo

Colors

Designer to choose colors to be used in the design.

Requirements
Must have
• An upbeat vibe - the logo looks great so inline with that !
Should not have
• anything old fashioned and old style fonts

```html
<!DOCTYPE html>
<html lang="en">
<head>
<meta charset="utf-8">
<title>VORTEQ – Innovation &amp; Technical Services</title>
<link href="https://fonts.googleapis.com/css2?family=Michroma&family=Lato:wght@400;700&display=swap" rel="stylesheet">
<style>
:root{
  --navy:#1d1d72;
  --navy-deep:#0d1f5c;
  --teal:#22d3c8;
  --ink:#1f1f1f;
  --muted:#555;
  --soft:#8a8a8a;
  --ice:#eafbfb;
  --tab-off:#9aa6cc;
  --footer:#434343;
  --white:#fff;
  --date:#1fb9c4;
  --display:'Michroma',sans-serif;
  --body:'Lato',sans-serif;
}
*{box-sizing:border-box;margin:0;padding:0}
html,body{width:1200px;height:3429px;overflow:hidden}
body{position:relative;font-family:var(--body);color:var(--ink);background:var(--white)}
.abs{position:absolute}
.btn{position:absolute;display:flex;align-items:center;justify-content:center;background:var(--navy);color:var(--white);font-family:var(--display);font-size:13px;letter-spacing:3px;border:2px solid var(--teal);box-shadow:0 3px 6px rgba(0,0,0,.2)}
.heading{position:absolute;display:flex;align-items:center;gap:14px;font-family:var(--display);letter-spacing:9px;color:#333;font-size:30px;white-space:nowrap}
.heading .mark{width:16px;height:16px;border-radius:50%;background:linear-gradient(135deg,var(--teal),var(--navy))}

/* header */
.site-header{position:absolute;left:0;top:0;width:1200px;height:103px;background:var(--white)}
.brand{position:absolute;left:107px;top:30px;display:flex;align-items:center;gap:10px}
.brand .dot{width:30px;height:30px;border-radius:50%;background:var(--navy)}
.brand .name{font-family:var(--display);font-size:26px;letter-spacing:5px;color:var(--navy)}
.brand .tag{position:absolute;left:40px;top:38px;font-family:var(--display);font-size:7px;letter-spacing:2px;color:var(--navy);white-space:nowrap}
.nav a{position:absolute;top:40px;font-size:16px;color:var(--ink);text-decoration:none}
.nav a.active{color:var(--navy);font-weight:700;border-bottom:2px solid var(--navy);padding-bottom:3px}

/* hero */
.hero{position:absolute;left:0;top:103px;width:1200px;height:583px;background:radial-gradient(circle at 68% 40%,#3a7cf0 0%,#1e4fb5 25%,#0f2e78 60%,#0b1f55 100%)}
.hero .bulb{position:absolute;left:600px;top:20px;width:440px;height:540px;border-radius:50% 50% 30% 30%;background:radial-gradient(circle at 50% 40%,rgba(180,215,255,.5),rgba(60,120,230,.15) 60%,transparent 75%)}
.hero .eyebrow{left:112px;top:142px;font-family:var(--display);color:var(--white);font-size:18px;letter-spacing:7px}
.hero h1{position:absolute;left:110px;top:178px;font-family:var(--display);font-weight:400;color:var(--white);font-size:52px;letter-spacing:14px}
.hero .sub{left:112px;top:260px;color:var(--white);font-size:16px;font-weight:700;letter-spacing:.3px}
.hero .lead{left:112px;top:294px;width:420px;color:var(--white);font-size:15px;line-height:29px}

/* about */
.about-art{left:173px;top:746px;width:310px;height:384px;border-radius:12px;background:linear-gradient(150deg,#5fe3dc 0%,#3aa8c8 40%,#2a3a9c 75%,#1d1d72 100%)}
.about .copy{left:573px;width:520px;font-size:15px;line-height:27.5px;color:#333}

/* services */
.services{position:absolute;left:0;top:1216px;width:1200px;height:698px;background:var(--ice)}
.tab{position:absolute;display:flex;align-items:center;justify-content:center;font-family:var(--display);font-size:13px;letter-spacing:3px;color:var(--white)}
.card{position:absolute;background:var(--white);border:1px solid #c9c9c9}
.card .photo{width:100%}
.svc-card h3{position:absolute;left:22px;font-size:18px;letter-spacing:1px;color:var(--navy-deep);font-weight:700}
.svc-card p{position:absolute;left:22px;width:400px;font-size:12.5px;line-height:24px;color:var(--muted)}

/* engineering */
.engineering{position:absolute;left:0;top:1914px;width:1200px;height:468px;background:radial-gradient(circle at 15% 55%,#2b5fb0 0%,#0f2a66 35%,#07123a 70%),#07123a}
.engineering .panel{position:absolute;left:229px;top:83px;width:743px;height:303px;border-radius:14px;background:var(--white)}
.engineering p{position:absolute;left:0;top:110px;width:743px;text-align:center;font-size:15px;line-height:31px;color:#333}

/* blog */
.post h4{position:absolute;left:18px;font-size:16.5px;font-weight:400;line-height:31px;letter-spacing:.5px;width:270px}
.post .date{position:absolute;left:18px;font-size:12.5px;font-weight:700;color:var(--date)}
.post p{position:absolute;left:18px;width:270px;font-size:12px;line-height:26px;color:var(--soft)}

/* footer */
.site-footer{position:absolute;left:0;top:3034px;width:1200px;height:332px;background:var(--footer);color:var(--white)}
.site-footer .brand{left:109px;top:120px}
.site-footer .brand .name,.site-footer .brand .tag{color:var(--white)}
.site-footer .brand .dot{background:var(--teal)}
.social{position:absolute;top:196px;width:32px;height:32px;border-radius:50%;background:var(--white)}
.col-title{position:absolute;top:82px;font-family:var(--display);font-size:13px;letter-spacing:3px}
.col-links a{position:absolute;font-size:15px;color:var(--white);text-decoration:none}
.contact-ico{position:absolute;left:894px;width:32px;height:32px;border-radius:50%;background:var(--white)}
.contact-txt{position:absolute;left:938px;font-size:15px;line-height:27px}
.copyright{position:absolute;left:0;top:3366px;width:1200px;height:63px;background:var(--navy);color:var(--white);display:flex;align-items:center;justify-content:center;font-size:16px;font-weight:700}
</style>
</head>
<body>

<header class="site-header">
  <div class="brand"><span class="dot"></span><span class="name">VORTEQ</span><span class="tag">INNOVATION &amp; TECHNICAL SERVICES</span></div>
  <nav class="nav">
    <a class="active" href="#" style="left:418px">HOME</a>
    <a href="#" style="left:521px">ABOUT</a>
    <a href="#" style="left:627px">SERVICES</a>
    <a href="#" style="left:755px">PRODUCT</a>
    <a href="#" style="left:884px">BLOG</a>
  </nav>
  <div class="btn" style="left:967px;top:29px;width:168px;height:43px;font-size:12px">CONTACT US</div>
</header>

<section class="hero" role="img" aria-label="Glowing wireframe light bulb on a deep blue technology background">
  <div class="bulb"></div>
  <div class="abs eyebrow">WELCOME TO</div>
  <h1>VORTEQ</h1>
  <div class="abs sub">INNOVATION &amp; TECHNICAL SERVICES</div>
  <div class="abs lead">Itaque earum rerum hic tenetur a sapiente delectus, ut quatur aut perferendis doloribus asperiores repellat.</div>
  <div class="btn" style="left:109px;top:373px;width:220px;height:53px;border-color:var(--white);background:transparent;box-shadow:none">GET STARTED</div>
</section>

<section class="about">
  <div class="abs about-art" role="img" aria-label="Abstract 3D swept shape in teal and navy"></div>
  <div class="heading" style="left:573px;top:752px"><span class="mark"></span>ABOUT VORTEQ</div>
  <p class="abs copy" style="top:804px">Nam libero tempore, cum soluta nobis est eligendi optio cumque nihil impedit quo minus id quod maxime placeat facere possimus, omnis voluptas assum enda est, omnis dolor repellendus. Temporibus autem quibusdam et aut offiiis debitis aut rerum necessitatibus saepe eveniet ut et voluptates repudiandae sint et molestiae non recusandae.</p>
  <p class="abs copy" style="top:969px">Itaque earum rerum hic tenetur a sapiente delectus, ut aut reiciendis sapiente delectus, ut aut reiciendis voluptatibus maiores alias consequatur aut perferendis doloribus asperiores repellat.</p>
  <div class="btn" style="left:573px;top:1072px;width:189px;height:51px">READ MORE</div>
</section>

<section class="services">
  <div class="heading" style="left:352px;top:58px"><span class="mark"></span>OUR SERVICES</div>
  <div class="tab" style="left:356px;top:136px;width:271px;height:51px;background:var(--navy);border:2px solid var(--teal)">LAUNDRY MARKET</div>
  <div class="tab" style="left:655px;top:136px;width:190px;height:51px;background:var(--tab-off)">PET TREAT</div>

  <article class="card svc-card" style="left:128px;top:233px;width:455px;height:393px">
    <div class="photo" role="img" aria-label="Bright laundry room with two front-loading washing machines and folded towels" style="height:248px;background:linear-gradient(135deg,#d9cdb8,#b9a98f 55%,#8a7b66)"></div>
    <h3 style="top:270px">HANGER ACCESSORY</h3>
    <p style="top:300px">Temporibus autem quibusdam et aut officiis debitis aut rerum necessitatibus saepe eveniet ut et voluptates repudiandae sint et molestiae non recusandae.</p>
  </article>
  <article class="card svc-card" style="left:617px;top:233px;width:455px;height:393px">
    <div class="photo" role="img" aria-label="Ginger cat eating dry treats from a white bowl" style="height:248px;background:linear-gradient(135deg,#b98a5a,#8f6a48 55%,#d8cfc4)"></div>
    <h3 style="top:270px">PET TREAT</h3>
    <p style="top:300px">Emporibus autem quibusdam et aut officiis debitis aut rerum necessitatibus saepe eveniet ut et voluptates repudiandae sint et molestiae non recusandae.</p>
  </article>
</section>

<section class="engineering" role="img" aria-label="Colourful fibre-optic light trails with a hand reaching in, dark blue tones">
  <div class="panel">
    <div class="heading" style="left:20px;top:48px"><span class="mark"></span>ABOUT ENGINEERING</div>
    <p>Itaque earum rerum hic tenetur a sapiente delectus, ut aut reiciendis voluptatibus maiores s<br>repellat.Temporibus t rerum necespudiandae sint et molestiae non recusandae.</p>
    <div class="btn" style="left:276px;top:192px;width:190px;height:50px">READ MORE</div>
  </div>
</section>

<section class="blog">
  <div class="heading" style="left:420px;top:2458px"><span class="mark"></span>OUR BLOG</div>

  <article class="card post" style="left:111px;top:2546px;width:304px;height:395px">
    <div class="photo" role="img" aria-label="Person wearing a VR headset surrounded by colourful light particles" style="height:225px;background:linear-gradient(135deg,#1a2a7a,#8a2aa8 50%,#d14fb0)"></div>
    <div class="date" style="top:245px">25 JAN 2025</div>
    <h4 style="top:267px">Temporibus autem quibusdam et aut officiis</h4>
    <p style="top:330px">Itaque earum rerum hic tenetur a sapiente delectus, ut aut reiciendis voluptatibus</p>
  </article>
  <article class="card post" style="left:449px;top:2546px;width:304px;height:395px">
    <div class="photo" role="img" aria-label="Engineer examining a small mechanical part in a laboratory" style="height:225px;background:linear-gradient(135deg,#c9a98c,#e8e2dc 50%,#b8bcc2)"></div>
    <div class="date" style="top:245px">27 FEB 2025</div>
    <h4 style="top:267px">Temporibus autem quibusdam et aut officiis</h4>
    <p style="top:330px">Itaque earum rerum hic tenetur a sapiente delectus, ut aut reiciendis voluptatibus</p>
  </article>
  <article class="card post" style="left:786px;top:2546px;width:304px;height:395px">
    <div class="photo" role="img" aria-label="Hand holding a glowing light bulb in front of a laptop" style="height:225px;background:radial-gradient(circle at 40% 45%,#f3c77a,#8a6a44 40%,#3b3a3a)"></div>
    <div class="date" style="top:245px">28 JAN 2025</div>
    <h4 style="top:267px">Temporibus autem quibusdam et aut officiis</h4>
    <p style="top:330px">Itaque earum rerum hic tenetur a sapiente delectus, ut aut reiciendis voluptatibus</p>
  </article>
</section>

<footer class="site-footer">
  <div class="brand"><span class="dot"></span><span class="name">VORTEQ</span><span class="tag">INNOVATION &amp; TECHNICAL SERVICES</span></div>
  <span class="social" style="left:130px" aria-label="Social link"></span>
  <span class="social" style="left:188px" aria-label="Social link"></span>
  <span class="social" style="left:245px" aria-label="Social link"></span>
  <span class="social" style="left:303px" aria-label="Social link"></span>

  <div class="col-title" style="left:457px">QUICK LINKS</div>
  <div class="col-links">
    <a href="#" style="left:459px;top:119px">Home</a>
    <a href="#" style="left:459px;top:153px">About</a>
    <a href="#" style="left:459px;top:188px">Services</a>
    <a href="#" style="left:459px;top:222px">Product</a>
    <a href="#" style="left:459px;top:256px">Contact</a>
  </div>
  <div class="col-title" style="left:674px">HELP LINKS</div>
  <div class="col-links">
    <a href="#" style="left:677px;top:119px">FAQ</a>
    <a href="#" style="left:677px;top:153px">Terms of use</a>
    <a href="#" style="left:677px;top:188px">Privacy Policy</a>
    <a href="#" style="left:677px;top:222px">Support Links</a>
    <a href="#" style="left:677px;top:256px">Conditions</a>
  </div>
  <div class="col-title" style="left:896px">CONTACT US</div>
  <span class="contact-ico" style="top:122px"><svg width="32" height="32" viewBox="0 0 32 32"><path d="M16 8a6 6 0 0 0-6 6c0 4.5 6 10 6 10s6-5.5 6-10a6 6 0 0 0-6-6z" fill="var(--footer)"/><circle cx="16" cy="14" r="2.2" fill="#fff"/></svg></span>
  <div class="contact-txt" style="top:120px">Vorteq<br>United States</div>
  <span class="contact-ico" style="top:184px"><svg width="32" height="32" viewBox="0 0 32 32"><path d="M11 9l3 0 1.5 4-2 1.5a9 9 0 0 0 4 4l1.5-2 4 1.5 0 3a2 2 0 0 1-2 2A13 13 0 0 1 9 11a2 2 0 0 1 2-2z" fill="var(--footer)"/></svg></span>
  <div class="contact-txt" style="top:186px">+1 888 888 8888</div>
  <span class="contact-ico" style="top:236px"><svg width="32" height="32" viewBox="0 0 32 32"><rect x="9" y="11" width="14" height="10" rx="1.5" fill="var(--footer)"/><path d="M9.5 12l6.5 5 6.5-5" stroke="#fff" stroke-width="1.4" fill="none"/></svg></span>
  <div class="contact-txt" style="top:238px">info@vorteqcom</div>
</footer>

<div class="copyright">Copyrights@2025.Vorteq.All Rights Reserved</div>

</body>
</html>
```